Creation of a Velmaro website

Velmaro is a company% 26 # 233; t% 26 # 233; consulting that accompanies Swiss companies or% 26 # 233; strang% 26 # 232; res in the d% 26 # 233; development of their business on the market% 26 # 233; Switzerland by providing strategic contacts (personalized contact program% 26 # 233; s) or market information% 26 # 233; (% 26 # 233; market research% 26 # 233;) and by providing administrative support (repr% 26 # 233; tax representation) or logistics (organization of% 26 # 233; v% 26 # 233; nement, assistance for participation% 26 # 224; fairs). Our customers are mainly European companies wishing to develop their business in Switzerland. N% 26 # 233; however, our services are% 26 # 233; also aimed at Swiss companies wishing to develop in other parts of Switzerland. Our site must therefore be% 26 # 234; capable of being translated into several languages. The services offered% 26 # 233; s by Velmaro may also% 26 # 233; also% 26 # 39;% 26 # 233; tender% 26 # 224; promoting tourism in Switzerland for countries or regions% 26 # 233; foreigners or% 26 # 224; the promotion of trade fairs or fairs with% 26 # 232; sd% 26 # 39; companies of the sectors concerned% 26 # 233; s. It is therefore n% 26 # 233; necessary to be able to add sub-headings of services which can% 26 # 234; be displayed% 26 # 233; es or hide% 26 # 233; es as required. We are 2 associates% 26 # 233; s, low% 26 # 233; s in the French-speaking parts (Neuch% 26 # 226; tel) and al% 26 # 233; manique (Zurich) of Switzerland.

Target Market(s)

Swiss or European companies wishing to develop their activities in Switzerland.

Coding

Coded - Design and coding required

Colors

Designer to choose colors to be used in the design.

Requirements
Must have
• A home page A section of% 26 # 233; writing the services offered% 26 # 233; es by Velmaro with the possibility% 26 # 233; d% 26 # 39; add sub-headings which can% 26 # 234; be displayed% 26 # 233; e or hidden% 26 # 233; e A page with the r% 26 # 233; f% 26 # 233; which can be displayed% 26 # 233; e or hidden% 26 # 233; e A page of% 26 # 233; writing l% 26 # 39;% 26 # 233; team A page with form contact, addresses and int card% 26 # 233; gr% 26 # 233; e The site must% 26 # 234; be low% 26 # 233; on a CMS allowing% 26 # 39;% 26 # 234; to be autonomous in modifying the website The possibility% 26 # 233; to be able to translate the site into several languages (FR, EN, DE, IT, NL, ...)

```html
<!DOCTYPE html>
<html lang="en">
<head>
<meta charset="utf-8">
<title>Velmaro – Business Consulting in Switzerland</title>
<link rel="stylesheet" href="https://fonts.googleapis.com/css2?family=Orbitron:wght@400;500;600&family=Barlow:wght@400;500;600&display=swap">
<style>
:root{
  --navy:#1b3246;
  --navy-deep:#10222f;
  --hero-a:#142a45;
  --hero-b:#2a4f78;
  --ice:#eef8fd;
  --ink:#1b3246;
  --grey:#5f6b74;
  --line:#d5dbe0;
  --white:#ffffff;
  --footer:#1a1c1e;
}
*{box-sizing:border-box;margin:0;padding:0}
html,body{width:1200px;height:3804px;overflow:hidden}
body{font-family:"Barlow",Arial,sans-serif;color:var(--ink);background:var(--white);position:relative}
.heading{font-family:"Orbitron",Arial,sans-serif;font-weight:500;text-transform:uppercase;letter-spacing:1px}
section,header,footer{position:relative;width:1200px;overflow:hidden}
.abs{position:absolute}
.center-x{left:0;right:0;text-align:center}
.section-title{font-size:29px;color:var(--ink)}
.section-sub{font-size:15px;color:var(--grey)}

/* Hero */
.hero{height:756px;background:linear-gradient(160deg,#0f2038 0%,var(--hero-a) 35%,var(--hero-b) 75%,#385f86 100%)}
.hero-photo{position:absolute;inset:0;background:radial-gradient(ellipse at 60% 55%,rgba(120,160,200,.35),transparent 60%),radial-gradient(ellipse at 20% 90%,rgba(70,120,170,.35),transparent 55%)}
.brand{position:absolute;left:111px;top:33px;display:flex;align-items:center;gap:24px;color:var(--white)}
.brand-mark{width:46px;height:46px;border-radius:8px;background:var(--white)}
.brand-name{font-family:"Orbitron",Arial,sans-serif;font-size:34px;font-weight:400;letter-spacing:3px;text-transform:uppercase}
.nav{position:absolute;top:47px;left:513px;font-family:"Orbitron",Arial,sans-serif;font-size:13px;color:var(--white)}
.nav a{color:var(--white);text-decoration:none;position:absolute;white-space:nowrap}
.nav .active{text-decoration:underline;text-underline-offset:3px}
.hero-title{top:270px;font-size:88px;font-weight:600;color:var(--white);letter-spacing:3px}
.hero-sub{top:382px;font-size:23px;line-height:37px;color:var(--white);letter-spacing:1px}
.btn-outline{display:inline-block;border:1.5px solid var(--white);color:var(--white);font-family:"Orbitron",Arial,sans-serif;font-size:14px;text-transform:uppercase;text-align:center}
.hero .btn-outline{position:absolute;left:518px;top:483px;width:162px;height:45px;line-height:42px;background:rgba(15,30,50,.35)}

/* Services */
.services{height:612px;background:var(--white)}
.service{position:absolute;border-radius:50%;text-align:center;display:flex;flex-direction:column;align-items:center}
.service.light{width:280px;height:280px;top:233px;background:var(--white);border:2px solid #e6e9ec;box-shadow:0 6px 14px rgba(0,0,0,.12);color:var(--ink)}
.service.dark{width:330px;height:330px;top:208px;left:435px;background:linear-gradient(180deg,#2a4a63 0%,var(--navy-deep) 100%);color:var(--white);z-index:2}
.service.dark::after{content:"";position:absolute;inset:14px;border:1px solid rgba(255,255,255,.55);border-radius:50%}
.service svg.icon{margin-top:36px}
.service.dark svg.icon{margin-top:48px}
.service h3{font-size:17px;margin-top:8px}
.service p{font-size:14px;line-height:25px;margin-top:10px;width:230px}
.service .toggle{margin-top:12px;width:50px;height:50px;border-radius:50%;border:1px solid currentColor;display:flex;align-items:center;justify-content:center;position:relative;z-index:3}

/* About */
.about{height:508px;background:var(--ice)}
.about-text{left:111px;top:160px;width:415px;font-size:13px;line-height:25.8px;color:var(--grey);text-align:justify}
.btn-solid{position:absolute;background:var(--navy);color:var(--white);font-family:"Orbitron",Arial,sans-serif;font-size:14px;text-transform:uppercase;text-align:center;border-radius:2px}
.about-art{left:576px;top:19px;width:487px;height:451px;background:radial-gradient(ellipse at 50% 55%,#cfe9f6 0%,#e3f3fb 50%,var(--ice) 75%)}

/* Team */
.team{height:549px;background:var(--navy);color:var(--white)}
.team .section-title,.team .section-sub{color:var(--white)}
.member{position:absolute;top:162px;width:240px;text-align:center}
.avatar{width:180px;height:180px;border-radius:50%;margin:0 auto;background:radial-gradient(circle at 50% 40%,#c9a88f 0%,#8a6e5c 55%,#5d5552 100%)}
.member h4{font-size:15px;margin-top:24px}
.member p{font-size:13.5px;line-height:19px;margin-top:8px;color:#dfe6ec}
.member .btn-outline{margin-top:18px;width:114px;height:40px;line-height:37px;font-size:13px;border-radius:2px}

/* News */
.news{height:660px;background:var(--white)}
.post{position:absolute;top:161px;width:315px}
.post-image{width:315px;height:227px}
.post-head{display:flex;gap:10px;margin-top:19px;align-items:center}
.date{width:65px;height:51px;background:var(--navy);color:var(--white);text-align:center;font-size:20px;line-height:20px;padding-top:5px;flex:none}
.post-head h5{font-size:14px;font-weight:500;line-height:23px;text-transform:uppercase;color:var(--ink)}
.post p{font-size:14px;line-height:27px;color:var(--grey);margin-top:18px}
.post .more{display:block;margin-top:12px;font-size:14px;font-weight:600;color:var(--ink);text-transform:uppercase;letter-spacing:.5px}

/* Contact */
.contact{height:472px;background:linear-gradient(180deg,#f3f5f7 0%,#f6f8fa 100%)}
.contact-bg{position:absolute;inset:0;background:radial-gradient(ellipse at 80% 70%,rgba(150,200,225,.25),transparent 55%),radial-gradient(ellipse at 10% 80%,rgba(150,200,225,.2),transparent 50%)}
.rule{left:573px;top:100px;width:56px;height:3px;background:var(--ink)}
.field{position:absolute;height:45px;background:var(--white);border:1px solid var(--line);font-size:14px;color:var(--grey);padding-left:14px;line-height:43px}

/* Footer */
.site-footer{height:247px;background:var(--footer);color:var(--white)}
.footer-brand{position:absolute;top:45px;left:0;right:0;display:flex;justify-content:center;align-items:center;gap:22px}
.footer-brand .brand-mark{width:44px;height:44px}
.footer-contacts{top:127px;font-size:14px;display:flex;justify-content:center;gap:30px;align-items:center}
.footer-contacts span{display:inline-flex;align-items:center;gap:8px}
.copyright{top:177px;font-size:13.5px}
</style>
</head>
<body>

<header class="hero">
  <div class="hero-photo" role="img" aria-label="Photo of hands typing on a laptop with a blue data overlay"></div>
  <div class="brand"><span class="brand-mark"></span><span class="brand-name">Velmaro</span></div>
  <nav class="nav">
    <a class="active" style="left:0">HOME</a>
    <a style="left:84px">ABOUT US</a>
    <a style="left:203px">SERVICES</a>
    <a style="left:321px">NEWS</a>
    <a style="left:409px">CONTACT US</a>
    <a style="left:520px;opacity:.8">|</a>
    <a style="left:535px">EN
      <svg width="10" height="6" viewBox="0 0 10 6" style="margin-left:8px"><path d="M0 0h10L5 6z" fill="#fff"/></svg></a>
  </nav>
  <h1 class="heading abs center-x hero-title">Velmaro</h1>
  <p class="heading abs center-x hero-sub" style="font-weight:400">Sed ut perspiciatis unde omnis iste natus<br>error sit voluptatem</p>
  <a class="btn-outline">Read More</a>
</header>

<section class="services">
  <h2 class="heading section-title abs center-x" style="top:64px">Our Services</h2>
  <p class="section-sub abs center-x" style="top:120px">Sed ut perspiciatis unde omnis iste natus error sit voluptatem accusantium doloremque laudantium</p>

  <div class="service light" style="left:177px">
    <svg class="icon" width="70" height="70" viewBox="0 0 70 70" fill="none" stroke="#1b3246" stroke-width="2"><path d="M12 8h30l10 10v44H12z"/><path d="M42 8v10h10"/><path d="M18 24h22M18 32h14"/><circle cx="24" cy="48" r="8"/><path d="M24 40v8h8"/><circle cx="48" cy="40" r="9"/><path d="M55 47l9 9"/></svg>
    <h3 class="heading">Market Research</h3>
    <p>Sed ut perspiciatis unde omnis acc usantium doloremque</p>
    <span class="toggle"><svg width="14" height="8" viewBox="0 0 14 8"><path d="M1 1l6 6 6-6" stroke="currentColor" stroke-width="1.8" fill="none"/></svg></span>
  </div>

  <div class="service dark">
    <svg class="icon" width="74" height="74" viewBox="0 0 74 74" fill="none" stroke="#fff" stroke-width="2"><path d="M14 6h40v56H14z"/><path d="M8 14h6M8 62c0 4 3 6 6 6h40"/><path d="M22 16h24M22 24h24M22 32h24M22 40h14"/><circle cx="52" cy="52" r="10"/><path d="M52 46v12M49 49h5M49 55h5"/></svg>
    <h3 class="heading">Tax Representation</h3>
    <p>Sed ut perspiciatis unde omnis acc usantium doloremque</p>
    <span class="toggle"><svg width="14" height="8" viewBox="0 0 14 8"><path d="M1 1l6 6 6-6" stroke="currentColor" stroke-width="1.8" fill="none"/></svg></span>
  </div>

  <div class="service light" style="left:744px">
    <svg class="icon" width="76" height="70" viewBox="0 0 76 70" fill="none" stroke="#1b3246" stroke-width="2"><circle cx="26" cy="10" r="7"/><path d="M16 62V30c0-6 4-10 10-10s10 4 10 10v8"/><path d="M20 62V44M32 62V44"/><path d="M40 36h24v26H40z"/><path d="M40 46h24M52 36v10"/></svg>
    <h3 class="heading">Logistics</h3>
    <p>Sed ut perspiciatis unde omnis acc usantium doloremque</p>
    <span class="toggle"><svg width="14" height="8" viewBox="0 0 14 8"><path d="M1 1l6 6 6-6" stroke="currentColor" stroke-width="1.8" fill="none"/></svg></span>
  </div>
</section>

<section class="about">
  <h2 class="heading section-title abs" style="left:111px;top:92px">About Us</h2>
  <p class="abs about-text">Velmaro is a company consulting that accompanies Swiss companies or strangers in the development of their business on the market wit zerland by providing strategic contacts (personalized contactprogram or market information ( market research) and by providing adminis trative support (repr tax representation) or logistics (organization of nement, assistance for participation fairs). Our customers are mainly wishing to develop their business in Switzerland.</p>
  <a class="btn-solid" style="left:111px;top:368px;width:132px;height:46px;line-height:46px">Read More</a>
  <div class="abs about-art" role="img" aria-label="Isometric illustration of a rising growth arrow, coin stacks and a person working at a laptop"></div>
</section>

<section class="team">
  <h2 class="heading section-title abs center-x" style="top:40px">Our Team</h2>
  <p class="section-sub abs center-x" style="top:92px">Sed ut perspiciatis unde omnis iste natus error sit voluptatem accusantium doloremque laudantium</p>
  <div class="member" style="left:109px">
    <div class="avatar" role="img" aria-label="Portrait photo of a team member"></div>
    <h4 class="heading">Jhon Smith</h4>
    <p>Sed ut perspiciatis unde &nbsp;iste<br>natus error sit</p>
    <a class="btn-outline">View Bio</a>
  </div>
  <div class="member" style="left:358px">
    <div class="avatar" role="img" aria-label="Portrait photo of a team member"></div>
    <h4 class="heading">Jhon Smith</h4>
    <p>Sed ut perspiciatis unde &nbsp;iste<br>natus error sit</p>
    <a class="btn-outline">View Bio</a>
  </div>
  <div class="member" style="left:608px">
    <div class="avatar" role="img" aria-label="Portrait photo of a team member"></div>
    <h4 class="heading">Jhon Smith</h4>
    <p>Sed ut perspiciatis unde &nbsp;iste<br>natus error sit</p>
    <a class="btn-outline">View Bio</a>
  </div>
  <div class="member" style="left:859px">
    <div class="avatar" role="img" aria-label="Portrait photo of a team member"></div>
    <h4 class="heading">Jhon Smith</h4>
    <p>Sed ut perspiciatis unde &nbsp;iste<br>natus error sit</p>
    <a class="btn-outline">View Bio</a>
  </div>
</section>

<section class="news">
  <h2 class="heading section-title abs center-x" style="top:51px">Latest News</h2>
  <p class="section-sub abs center-x" style="top:104px">Sed ut perspiciatis unde omnis iste natus error sit voluptatem accusantium doloremque laudantium</p>

  <article class="post" style="left:111px">
    <div class="post-image" role="img" aria-label="Photo of hands on a laptop with a blue digital overlay" style="background:linear-gradient(160deg,#1d2f6e,#3b5fae 55%,#1a2a52)"></div>
    <div class="post-head"><div class="date">05<br>JAN</div><h5>Sed ut perspiciatis unde omni<br>iste natus error sit</h5></div>
    <p>Nemo enim ipsam voluptatem quia voluptas sit aspernatur aut odit aut fugit, sed quia conse qu dolores eos qui ratione voluptatem</p>
    <a class="more">Read More</a>
  </article>

  <article class="post" style="left:443px">
    <div class="post-image" role="img" aria-label="Photo of a businessman using a laptop at a desk" style="background:linear-gradient(160deg,#8fa3b6,#3f5a78 55%,#1d2c3f)"></div>
    <div class="post-head"><div class="date">05<br>JAN</div><h5>Sed ut perspiciatis unde omni<br>iste natus error sit</h5></div>
    <p>Nemo enim ipsam voluptatem quia voluptas sit aspernatur aut odit aut fugit, sed quia conse qu dolores eos qui ratione voluptatem</p>
    <a class="more">Read More</a>
  </article>

  <article class="post" style="left:773px">
    <div class="post-image" role="img" aria-label="Photo of a hand with a pen over financial charts" style="background:linear-gradient(160deg,#c9b8a6,#6d6a68 50%,#2a3036)"></div>
    <div class="post-head"><div class="date">05<br>JAN</div><h5>Sed ut perspiciatis unde omni<br>iste natus error sit</h5></div>
    <p>Nemo enim ipsam voluptatem quia voluptas sit aspernatur aut odit aut fugit, sed quia conse qu dolores eos qui ratione voluptatem</p>
    <a class="more">Read More</a>
  </article>
</section>

<section class="contact">
  <div class="contact-bg" role="img" aria-label="Faint background of marketing words printed on paper"></div>
  <h2 class="heading section-title abs center-x" style="top:48px">Contact Us</h2>
  <div class="abs rule"></div>
  <p class="section-sub abs center-x" style="top:126px;font-size:14px">Sed ut perspiciatis unde omnis iste natus error sit voluptatem accusantium doloremque</p>
  <div class="field" style="left:273px;top:180px;width:318px">First Name*</div>
  <div class="field" style="left:608px;top:180px;width:318px">Last Name*</div>
  <div class="field" style="left:273px;top:235px;width:318px">Phone*</div>
  <div class="field" style="left:608px;top:235px;width:318px">Email*</div>
  <div class="field" style="left:273px;top:291px;width:653px">Company*</div>
  <a class="btn-solid" style="left:524px;top:357px;width:152px;height:45px;line-height:45px;font-size:17px">Submit</a>
</section>

<footer class="site-footer">
  <div class="footer-brand"><span class="brand-mark"></span><span class="brand-name">Velmaro</span></div>
  <div class="abs center-x footer-contacts">
    <span><svg width="10" height="14" viewBox="0 0 10 14"><path d="M5 0a5 5 0 0 0-5 5c0 4 5 9 5 9s5-5 5-9a5 5 0 0 0-5-5zm0 7a2 2 0 1 1 0-4 2 2 0 0 1 0 4z" fill="#fff"/></svg>No. 3, lorem ipsum Street,lorem ipsum</span>
    <span>|</span>
    <span><svg width="13" height="10" viewBox="0 0 13 10"><path d="M0 0h13v10H0z" fill="#fff"/><path d="M0 0l6.5 5L13 0" stroke="#1a1c1e" stroke-width="1.2" fill="none"/></svg>info@velmaro.com</span>
    <span>|</span>
    <span><svg width="12" height="12" viewBox="0 0 12 12"><path d="M2 0l2.5 2.5L3 4.5c1 2 2.5 3.5 4.5 4.5L9.5 7.5 12 10l-2 2C4.5 11.5.5 7.5 0 2z" fill="#fff"/></svg>000.454.7788</span>
  </div>
  <p class="abs center-x copyright">© Copyright 2020 Velmaro.All Rights Reserved</p>
</footer>

</body>
</html>
```